Meal Plan Website Needs New Pages Designed

Brightwick Supper Kits is an online, membership based program that delivers weekly meal programs (7 days worth of recipes plus shopping lists) carefully crafted by an expert team of meal planners. All recipes are created to comply with the following macronutrient ratio: 65% healthy fats, 25% lean protein, 10% good carbs.
All recipes are Paleo friendly and a great resource for those individuals who want to correctly implement this type of diet.

We are re-designing our website and need the following pages designed:

· Home page w/ logo
· How it works page
· Get Started! page
· Recipes Page template (these will be the pages on our site that will have recipes)
· Kitchen Essentials Training page (this will be a page with videos and tips + tricks, PDFs, etc)

So 5 total PSDs, 1 for each page.

Target audience: Men and women between the ages of 30 and 60 who want to:
· Eat healthy
· Lose weight
· Follow/Implement the Paleo diet
· Take the guesswork out of preparing delicious AND healthy meals for them and their families
· Know exactly what to eat, what to buy, how to make it

Feelings/Messages we want to communicate through the design:
· “Organic” but elegant look
· Fresh/light/Airy
· Simple but NOT GENERIC
· “I want to get cooking” feeling

Our Stylistic preferences:
· Minimalist with a few bold elements (something in between)
· Easy to visually navigate (enough white space, but not too much)
· There is more to “see” than to “read”

Our Color Preferences:
· Lighter pallet
· Colors that evoke natural woods, granite countertops…
· Stay away from using all dark colors

Our Font Type Preferences:
· Easy to read
· Not more than 3 font types
· Not too rigid
· Not too sophisticated
· Simple with a touch

Examples of Website Designs that we like:
· http://www.dorvanta.com/meal-plans/
· http://grulvix.com/
· https://www.mistobarn.com/

```html
<!DOCTYPE html>
<html lang="en">
<head>
<meta charset="utf-8">
<title>Brightwick Supper Kits – Home</title>
<link href="https://fonts.googleapis.com/css2?family=Cabin:wght@400;500;600;700&family=Open+Sans:wght@400;600&display=swap" rel="stylesheet">
<style>
:root{
  --wood:#f4e9dc;
  --wood-deep:#ecdcc8;
  --bark:#5e524d;
  --bark-dark:#4e4440;
  --green:#5e9f80;
  --green-dark:#3f7b60;
  --ink:#4c433f;
  --muted:#7b716b;
  --panel:#f6f2ed;
  --sand:#ebdcc7;
  --white:#ffffff;
  --rule:#c9b9a6;
}
*{box-sizing:border-box;margin:0;padding:0}
html,body{width:1200px;height:2528px;overflow:hidden}
body{position:relative;font-family:"Open Sans",Arial,sans-serif;color:var(--ink);
  background:linear-gradient(180deg,#f5ebdf 0%,var(--wood) 50%,#f1e4d4 100%)}
.abs{position:absolute}

/* top bar */
.topbar{left:0;top:0;width:1200px;height:54px;background:var(--bark)}
.toplinks{left:133px;top:17px;font:600 13px "Cabin",sans-serif;color:#fff;letter-spacing:.3px}
.toplinks span{margin:0 8px;color:#cfc6c0}
.search{left:820px;top:12px;width:247px;height:30px;background:#6e625c;border:1px solid #85786f;
  font-size:12px;color:#d8d0ca;padding:7px 10px}
.search svg{position:absolute;right:8px;top:7px}

/* header */
.brand{left:131px;top:95px;display:flex;align-items:center;gap:12px}
.brand-dot{width:28px;height:28px;border-radius:50%;background:var(--bark)}
.brand-name{font:700 25px "Cabin",sans-serif;color:var(--green);letter-spacing:.3px}
.findus{left:615px;top:101px;font:500 13px "Cabin",sans-serif;color:var(--ink)}
.social{left:688px;top:95px;display:flex;gap:8px}
.social i{display:block;width:30px;height:30px;border-radius:50%}
.signup{left:849px;top:91px;width:218px;height:40px;background:var(--bark);color:#fff;
  font:600 13px "Cabin",sans-serif;display:flex;align-items:center;justify-content:center;border-radius:2px}

/* nav ribbon */
.ribbon{left:51px;top:157px}
.nav{left:115px;top:160px;width:972px;height:52px;
  font:500 16px "Cabin",sans-serif;color:#fff;text-transform:uppercase}
.nav a{color:#fff;text-decoration:none;position:absolute;top:16px;white-space:nowrap}
.nav a.current{color:var(--bark-dark)}

/* hero */
.hero{left:133px;top:246px;width:934px;height:408px;background:var(--panel);border:4px solid var(--white);overflow:hidden}
.hero-title{left:38px;top:70px;font:600 26px "Cabin",sans-serif;color:var(--bark-dark);white-space:nowrap}
.hero-sub{left:38px;top:110px;font:600 25px "Cabin",sans-serif;color:var(--green);white-space:nowrap}
.hero-copy{left:38px;top:166px;width:550px;font-size:12.5px;line-height:20px;color:var(--muted)}
.hero-price{left:38px;top:250px;font:500 19px "Cabin",sans-serif;color:var(--bark-dark);white-space:nowrap}
.btn-start{left:38px;top:308px;width:161px;height:42px;background:var(--green);color:#fff;
  font:600 18px "Cabin",sans-serif;display:flex;align-items:center;justify-content:center}
.hero-media{right:0;top:0}
.arrow{width:37px;height:37px;border-radius:50%;border:2px solid var(--bark);background:#fff;top:434px}

/* dividers */
.divider{left:130px;width:937px;height:20px}
.divider::before,.divider::after{content:"";position:absolute;top:9px;height:1px;background:var(--rule);width:430px}
.divider::before{left:0}.divider::after{right:0}
.divider .mark{position:absolute;left:438px;top:4px;width:60px;height:12px;border-radius:6px;background:#b9a895}

.section-title{left:130px;width:937px;text-align:center;font:500 22px "Cabin",sans-serif;color:var(--ink)}
.intro{left:130px;top:780px;width:937px;text-align:center;font-size:12.5px;line-height:24px;color:var(--muted)}

/* stat boxes */
.stat{top:947px;width:286px;height:155px;background:var(--panel);border:4px solid var(--white)}
.stat h3{position:absolute;left:32px;top:20px;font:500 30px "Cabin",sans-serif;color:var(--bark-dark);white-space:nowrap}
.stat small{position:absolute;left:34px;top:63px;font:600 12px "Cabin",sans-serif;color:var(--bark-dark)}
.stat strong{position:absolute;left:32px;top:84px;font:700 48px "Cabin",sans-serif;color:var(--green)}
.stat .icon{position:absolute;left:170px;top:64px;width:68px;height:62px;border-radius:6px;background:#6a5d56}

/* why box */
.why{left:133px;top:1147px;width:934px;height:204px;background:var(--sand);border:5px solid var(--white)}
.why .plate{position:absolute;left:34px;top:50px;width:106px;height:90px;border-radius:50%;background:#d8c6ae}
.why h2{position:absolute;left:186px;top:48px;font:700 22px "Cabin",sans-serif;color:var(--green);white-space:nowrap}
.why p{position:absolute;left:186px;top:90px;width:715px;font-size:12.5px;line-height:24px;color:var(--muted)}

/* cards */
.card{top:1495px;width:280px}
.card .photo{width:280px;height:246px;border:6px solid var(--white)}
.card h4{margin-top:29px;font:500 16px "Cabin",sans-serif;color:var(--ink);white-space:nowrap}
.card p{margin-top:10px;font-size:12px;line-height:24px;color:var(--muted)}
.card .actions{margin-top:14px;display:flex;align-items:center;height:25px}
.learn{font:600 14px "Cabin",sans-serif;color:var(--bark-dark);display:flex;align-items:center;gap:8px;width:134px;padding-left:14px}
.join{display:flex;height:25px}
.join b{width:32px;background:var(--bark);color:#fff;font:700 18px/25px "Cabin",sans-serif;text-align:center}
.join span{width:80px;background:var(--green);color:#fff;font:600 13px/25px "Cabin",sans-serif;text-align:center}

/* cta */
.cta{left:131px;top:1977px;width:938px;height:190px;background:var(--green);border:5px solid var(--white)}
.cta p{position:absolute;left:30px;top:22px;width:868px;text-align:center;color:#fff;
  font:500 15.5px "Cabin",sans-serif;line-height:30px;text-transform:uppercase}
.cta .guide{position:absolute;left:346px;top:122px;width:236px;height:44px;border:2px solid #fff;border-radius:3px;
  color:#fff;font:600 15px "Cabin",sans-serif;display:flex;align-items:center;justify-content:center}

/* footer */
.footer{left:0;top:2199px;width:1200px;height:329px;background:var(--bark)}
.f-col{top:2240px;color:#e9e2dc}
.f-col h5{font:500 22px "Cabin",sans-serif;color:#e4ddd7;margin-bottom:18px}
.f-brand{font:700 23px/26px "Cabin",sans-serif;color:#ece5df;display:flex;gap:12px;align-items:flex-start}
.f-brand i{width:26px;height:26px;border-radius:50%;background:#e4ddd7;margin-top:2px;flex:none}
.f-text{font-size:12px;line-height:23px;color:#e0d8d2}
.f-links li{list-style:none;display:flex;align-items:center;gap:12px;height:32px;font-size:12.5px}
.f-links i{width:26px;height:26px;border-radius:50%;display:block}
.f-addr li{list-style:none;display:flex;gap:12px;font-size:12px;line-height:25px;color:#e0d8d2;white-space:nowrap}
.f-addr svg{flex:none;margin-top:6px}
.f-addr .indent{padding-left:26px}
.news-input{display:flex;margin-top:16px;width:211px;height:26px}
.news-input span{flex:1;border:1px solid #9a8d85;font-size:11px;color:#cfc5be;padding:5px 6px}
.news-input b{width:61px;background:var(--green);color:#fff;font:600 12px/26px "Cabin",sans-serif;text-align:center}
.f-rule{left:0;top:2460px;width:1200px;height:1px;background:#76695f}
.copyright{left:0;top:2484px;width:1200px;text-align:center;font-size:11.5px;color:#f0ebe7}
</style>
</head>
<body>

<!-- Top bar -->
<div class="abs topbar"></div>
<div class="abs toplinks">OUR EXPERTS<span>|</span>SUPPORT<span>|</span>MEMBER LOG IN</div>
<div class="abs search">Enter any keywords
  <svg width="16" height="16" viewBox="0 0 16 16"><circle cx="6.5" cy="6.5" r="4.5" fill="none" stroke="#fff" stroke-width="2"/><line x1="10" y1="10" x2="14" y2="14" stroke="#fff" stroke-width="2.4"/></svg>
</div>

<!-- Header -->
<div class="abs brand"><i class="brand-dot"></i><span class="brand-name">BRIGHTWICK SUPPER KITS</span></div>
<div class="abs findus">Find Us On:</div>
<div class="abs social">
  <i style="background:#3b6fb0"></i><i style="background:#3b98cc"></i><i style="background:#cc3b48"></i><i style="background:#e09a2c"></i>
</div>
<div class="abs signup">SIGN UP FOR THE MEAL PLAN</div>

<!-- Navigation ribbon -->
<svg class="abs ribbon" width="1098" height="66" viewBox="0 0 1098 66">
  <polygon points="0,14 64,14 64,58 0,58 22,36" fill="#4e8d70"/>
  <polygon points="1098,14 1034,14 1034,58 1098,58 1076,36" fill="#4e8d70"/>
  <polygon points="64,58 64,50 78,58" fill="#2f5e48"/>
  <polygon points="1034,58 1034,50 1020,58" fill="#2f5e48"/>
  <rect x="64" y="0" width="970" height="58" fill="#5e9f80"/>
  <line x1="64" y1="5" x2="1034" y2="5" stroke="#8cc2a7" stroke-dasharray="4 3"/>
  <line x1="64" y1="53" x2="1034" y2="53" stroke="#8cc2a7" stroke-dasharray="4 3"/>
</svg>
<nav class="abs nav">
  <a class="current" style="left:38px">Home</a>
  <a style="left:152px">What is Meal Plan?</a>
  <a style="left:376px">Resources</a>
  <a style="left:527px">Recipe Center</a>
  <a style="left:697px">Success Stories</a>
  <a style="left:893px">Blog</a>
</nav>

<!-- Hero -->
<section class="abs hero">
  <svg class="abs hero-media" width="310" height="400" viewBox="0 0 310 400" role="img" aria-label="Photo of a smiling chef in white uniform behind a table of fresh vegetables">
    <defs>
      <linearGradient id="heroFill" x1="0" y1="0" x2="0" y2="1">
        <stop offset="0" stop-color="#ffffff"/>
        <stop offset=".62" stop-color="#eeebe6"/>
        <stop offset="1" stop-color="#9fbf86"/>
      </linearGradient>
    </defs>
    <path d="M54,0 Q-20,200 50,400 L310,400 L310,0 Z" fill="url(#heroFill)"/>
    <path d="M54,0 Q-20,200 50,400" fill="none" stroke="#ddd8d1" stroke-width="3"/>
  </svg>
  <h1 class="abs hero-title">NEQUE PORRO QUISQUAM EST QUI DOLOREM</h1>
  <h2 class="abs hero-sub">IPSUM QUIA DOLOR SIT AMET</h2>
  <p class="abs hero-copy">Lorem ipsum dolor sit amet, consectetur adipisicing elit, sed do eiusmod tempor incididunt ut labore et dolore magna aliqua. Ut enim ad minim veniam, quis nostrud exercitation ullamco laboris nisi ut aliquip ex ea commodo consequat. Duis aute irure dolor in.</p>
  <p class="abs hero-price">Starting at less than $8/month 14-day free trial on all plans</p>
  <div class="abs btn-start">GET STARTED</div>
</section>
<svg class="abs arrow" style="left:115px" viewBox="0 0 37 37"><polygon points="22,11 13,18.5 22,26" fill="#5e524d"/></svg>
<svg class="abs arrow" style="left:1048px" viewBox="0 0 37 37"><polygon points="15,11 24,18.5 15,26" fill="#5e524d"/></svg>

<!-- Intro -->
<div class="abs divider" style="top:689px"><span class="mark" role="img" aria-label="Decorative flourish"></span></div>
<h2 class="abs section-title" style="top:734px">Neque porro quisquam est qui dolorem ipsum quia dolor sit amet, consecpsum quia dolor</h2>
<p class="abs intro">Sed ut perspiciatis unde omnis iste natus error sit voluptatem accusantium doloremque laudantium, totam rem aperiam, eaque ipsa quae ab illo inventore veritatis et quasi architecto beatae vitae dicta sunt explicabo. Nemo enim ipsam voluptatem quia voluptas sit aspernatur aut odit aut fugit, sed quia c uuntur magni dolores eos qui ratione voluptatem sequi nesciunt. Neque porro quisquam est, qui dolorem ipsum quia dolor sit amet, consectetur, elit, sed quia non numquam eius modi tempora incidunt ut labore et dolore magnam aliquam quaerat voluptatem.</p>
<div class="abs divider" style="top:888px"><span class="mark" role="img" aria-label="Decorative flourish"></span></div>

<!-- Macronutrient stats -->
<div class="abs stat" style="left:133px"><h3>HEALTHY FATS</h3><small>OF THE WEEK</small><strong>65%</strong><span class="icon" role="img" aria-label="Icon of a burger and a drink cup"></span></div>
<div class="abs stat" style="left:456px"><h3>LEAN PROTEIN</h3><small>OF THE WEEK</small><strong>25%</strong><span class="icon" role="img" aria-label="Icon of an ear of corn"></span></div>
<div class="abs stat" style="left:779px"><h3>GOOD CARBS</h3><small>OF THE WEEK</small><strong>10%</strong><span class="icon" role="img" aria-label="Icon of a burger"></span></div>

<!-- Why box -->
<section class="abs why">
  <span class="plate" role="img" aria-label="Large plate emblem"></span>
  <h2>WHY SHOULD I EAT BRIGHTWICK SUPPER KITS ?</h2>
  <p>Sed ut perspiciatis unde omnis iste natus error sit voluptatem accusantium doloremque laudantium, totam rem aperiam veritatis et quasi architecto beatae vitae dicta sunt explicabo. Nemo enim ipsam voluptatem quia voluptas sit asper uuntur magni dolores eos qui ratione voluptatem sequi nesciunt.</p>
</section>

<!-- Plans -->
<div class="abs divider" style="top:1387px"><span class="mark" role="img" aria-label="Decorative flourish"></span></div>
<h2 class="abs section-title" style="top:1432px">Neque porro quisquam est qui dolorem ipsum quia dolor sit amet, consecpsum quia dolor</h2>

<article class="abs card" style="left:131px">
  <div class="photo" role="img" aria-label="Photo of layered lasagna with meat sauce" style="background:linear-gradient(160deg,#f3d88a,#e2b457 45%,#b5562c 75%,#f1e1b4)"></div>
  <h4>Biorbjg Our vegetarian plans are simple</h4>
  <p>Sed ut perspiciatis unde omnis iste naxzcvctus erro veritatis et quasi architecto plans are simple</p>
  <div class="actions"><span class="learn"><svg width="8" height="10"><polygon points="0,0 8,5 0,10" fill="#4e4440"/></svg>LEARN MORE</span><span class="join"><b>+</b><span>JOIN NOW</span></span></div>
</article>
<article class="abs card" style="left:459px">
  <div class="photo" role="img" aria-label="Photo of a bowl of bean chili with fresh herbs" style="background:linear-gradient(160deg,#3a2a22,#8c3a1f 45%,#6f8b3a 70%,#2e211b)"></div>
  <h4>Biorbjg Our vegetarian plans are simple</h4>
  <p>Sed ut perspiciatis unde omnis iste naxzcvctus erro veritatis et quasi architecto plans are simple</p>
  <div class="actions"><span class="learn"><svg width="8" height="10"><polygon points="0,0 8,5 0,10" fill="#4e4440"/></svg>LEARN MORE</span><span class="join"><b>+</b><span>JOIN NOW</span></span></div>
</article>
<article class="abs card" style="left:784px">
  <div class="photo" role="img" aria-label="Photo of a meat pie slice topped with parsley" style="background:linear-gradient(160deg,#d8c8b6,#c98b52 40%,#7c3320 70%,#e9dcc9)"></div>
  <h4>Biorbjg Our vegetarian plans are simple</h4>
  <p>Sed ut perspiciatis unde omnis iste naxzcvctus erro veritatis et quasi architecto plans are simple</p>
  <div class="actions"><span class="learn"><svg width="8" height="10"><polygon points="0,0 8,5 0,10" fill="#4e4440"/></svg>LEARN MORE</span><span class="join"><b>+</b><span>JOIN NOW</span></span></div>
</article>

<div class="abs divider" style="top:1931px"><span class="mark" role="img" aria-label="Decorative flourish"></span></div>

<!-- Guide CTA -->
<section class="abs cta">
  <p>More info: your guide to paleo is a beautiful guide created for everything you need to know about Brightwick Supper Kits the guide will help you avoid the most common pitfalls and reach your goals much faster.</p>
  <div class="guide">CHECK OUT THE GUIDE NOW!</div>
</section>

<!-- Footer -->
<footer class="abs footer"></footer>
<div class="abs f-col" style="left:131px;width:250px">
  <div class="f-brand"><i></i><span>BRIGHTWICK<br>SUPPER KITS</span></div>
  <p class="f-text" style="margin-top:18px">Lorem ipsum dolor sit amet, consectetur adipisicing elit, sed do eiusmod tebmpor incididunt ut labore et dolore magn liqua. Ut enim ad minim veniamzfggle ostrud exercitation ullamco</p>
</div>
<div class="abs f-col" style="left:430px;width:180px">
  <h5>LINKS</h5>
  <ul class="f-links">
    <li><i style="background:#3b98cc"></i>Chirpwire</li>
    <li><i style="background:#e09a2c"></i>RSS feed</li>
    <li><i style="background:#3b6fb0"></i>Pagemates</li>
    <li><i style="background:#cc3b48"></i>Tunewell</li>
  </ul>
</div>
<div class="abs f-col" style="left:629px;width:220px">
  <h5>ADDRESS</h5>
  <ul class="f-addr">
    <li><svg width="14" height="12" viewBox="0 0 14 12"><polygon points="7,0 14,6 12,6 12,12 2,12 2,6 0,6" fill="#e4ddd7"/></svg>Halvern Loan Partners, LLC</li>
    <li class="indent">4127 Tamsin Ave., #212</li>
    <li class="indent">Westmere, CA 90412</li>
    <li><svg width="14" height="12" viewBox="0 0 14 12"><path d="M3,0 L5,3 L4,5 Q6,8 8,8 L10,7 L13,9 L11,12 Q2,11 1,2 Z" fill="#e4ddd7"/></svg>Call us: 555-014-2287</li>
    <li><svg width="14" height="12" viewBox="0 0 14 12"><rect x="3" y="0" width="8" height="12" rx="1" fill="none" stroke="#e4ddd7" stroke-width="1.5"/></svg>Fax us: 555-014-2290</li>
    <li><svg width="14" height="12" viewBox="0 0 14 12"><rect x="1" y="2" width="12" height="8" fill="#e4ddd7"/><polyline points="1,2 7,7 13,2" fill="none" stroke="#5e524d"/></svg>Email us: info@halvernloans.com</li>
  </ul>
</div>
<div class="abs f-col" style="left:856px;width:212px">
  <h5>NEWSLETTER</h5>
  <p class="f-text">Excepteur sint occaecat cupidatat non p roident, sunt in culpa qui officia deserunt mollit anim id est laborum.</p>
  <div class="news-input"><span>Enter email address</span><b>SIGNUP</b></div>
</div>
<div class="abs f-rule"></div>
<div class="abs copyright">Copyright © 2014 Brightwick Supper Kits, LLC. All rights reserved.</div>

</body>
</html>
```